Marble Orchard - Report on digital habits and attitudes

We are a research company and we have written a PowerPoint Report to present the results of a series of surveys conducted in the last three years. The research is about the "Marble Orchard": people are facing the opportunities and challanges of their lives transformed by the digital technologies. We have investigated a number of topics through thousands of interviews and we've analyzed the data presented in the PowerPoint document.
We're not quite satisfied with the look and feel of the report: it looks too flat and boring, too "basic" to be presented as a professional work, yet being just that. We'd like you to upgrade the graphics and style of the report up to the level of a professional research product. The document still needs to be fully editable (either text and charts) but you can rearrange all the contents as you please, adding images, changing font and text size, colors and whatever you think is necessary to reach our goal.

Target Market(s)

Media covering digital issues
Marketing executives
Public institutions and policy makers

Industry/Entity Type

Market Research

Requirements
Must have
• The treats of a professional work
Fully editable within PowerPoint (either text and charts)
Nice to have
• Smart images
Original organization of the pages
Colors and graphics coherent with the quillbrook.it logo/website look and feel
Should not have
• PPT document over 30 MBytes
Images violating copyright

```html
<!DOCTYPE html>
<html lang="it">
<head>
<meta charset="utf-8">
<title>Marble Orchard – Report Quillbrook</title>
<link href="https://fonts.googleapis.com/css2?family=Roboto:wght@400;500;700&display=swap" rel="stylesheet">
<style>
  :root {
    --canvas: #efefef;
    --slate: #7a7f8e;
    --amber: #c0691f;
    --ink-light: #ffffff;
    --text-soft: rgba(255,255,255,0.85);
    --chart-label: #f6efe0;
    --dot: #a9c14b;
    --dot-edge: #8aa23a;
    --chart-bg: rgba(240,240,240,0.92);
  }
  * { box-sizing: border-box; margin: 0; padding: 0; }
  html, body { width: 1200px; height: 1021px; overflow: hidden; background: var(--canvas); }
  body { position: relative; font-family: "Roboto", sans-serif; color: var(--ink-light); }

  .slide {
    position: absolute; width: 558px; height: 299px; overflow: hidden;
    background: linear-gradient(30deg, var(--slate) 0%, #978066 50%, var(--amber) 100%);
  }
  .slide--white { background: #ffffff; box-shadow: 0 0 0 1px #e2e2e2; }
  .pos-a { left: 22px; top: 33px; }
  .pos-b { left: 612px; top: 33px; }
  .pos-c { left: 22px; top: 362px; }
  .pos-d { left: 612px; top: 358px; }
  .pos-e { left: 22px; top: 690px; }
  .pos-f { left: 615px; top: 683px; }

  .brand { position: absolute; display: flex; flex-direction: column; align-items: center; gap: 3px; }
  .brand__dot { width: 9px; height: 9px; border: 1.5px solid var(--ink-light); border-radius: 50%; }
  .brand__name { font-size: 5px; font-weight: 500; letter-spacing: 1.2px; color: var(--ink-light); }

  /* cover */
  .cover__title { position: absolute; left: 17px; top: 178px; font-weight: 700; font-size: 28px; line-height: 37px; }
  .cover__visual {
    position: absolute; left: 295px; top: 32px; width: 246px; height: 246px; border-radius: 50%;
    background: radial-gradient(circle, #e8a72e 0 54%, #7a1431 55% 63%, #1c3c6e 64% 92%, #7f9b35 93%);
  }

  /* break */
  .break__art {
    position: absolute; left: 83px; top: 74px; width: 388px; height: 148px; border-radius: 40px;
    background: linear-gradient(90deg, #5fae3b, #2f7fd0 25%, #f0c51a 45%, #e3262b 60%, #f6c21b 75%, #2d7ad1);
    opacity: 0.85;
  }

  /* index */
  .index__title { position: absolute; left: 33px; top: 44px; font-size: 30px; font-weight: 700; }
  .index__row { position: absolute; font-size: 18px; font-weight: 700; display: flex; align-items: center; gap: 5px; }
  .index__row::before { content: ""; width: 5px; height: 5px; border: 1px solid var(--ink-light); border-radius: 50%; }
  .index__num { position: absolute; font-size: 18px; font-weight: 700; }

  /* hopes */
  .hopes__title { position: absolute; left: 23px; top: 26px; font-size: 20px; font-weight: 700; color: #eeeeee; }
  .para { position: absolute; font-size: 7px; line-height: 12.4px; color: var(--text-soft); }
  .chart-title { position: absolute; font-size: 11px; font-weight: 700; color: var(--chart-label); }
  .chart { position: absolute; width: 135px; height: 108px; background: var(--chart-bg); }
  .chart text { font-family: "Roboto", sans-serif; }

  /* about */
  .about__title { position: absolute; left: 14px; top: 32px; font-size: 38px; font-weight: 700; letter-spacing: 0.5px; }
  .about__photo { position: absolute; left: 382px; top: 55px; width: 162px; height: 206px;
    background: radial-gradient(circle at 70% 40%, #6f6f6f, #1a1a1a 60%, #050505); }
  .about__block { position: absolute; width: 166px; }
  .about__block h3 { font-size: 9px; font-weight: 700; margin-bottom: 5px; }
  .about__block p { font-size: 6.6px; line-height: 12.8px; color: var(--text-soft); }
  .about__rule-h { position: absolute; left: 14px; top: 171px; width: 360px; height: 1px; background: rgba(255,255,255,0.6); }
  .about__rule-v { position: absolute; left: 195px; top: 89px; width: 1px; height: 176px; background: rgba(255,255,255,0.6); }
  .about__node { position: absolute; left: 183px; top: 162px; width: 24px; height: 24px; border-radius: 50%; background: #fff; }
  .about__node::after { content: ""; position: absolute; left: 8px; top: 7px; width: 8px; height: 8px; border: 1.5px solid var(--amber); border-radius: 50%; }

  .thanks { position: absolute; left: 0; right: 0; top: 130px; text-align: center; font-size: 28px; font-weight: 700; }
</style>
</head>
<body>

<section class="slide pos-a">
  <div class="brand" style="left:12px; top:8px;"><span class="brand__dot"></span><span class="brand__name">QUILLBROOK</span></div>
  <h1 class="cover__title">OMO<br>OSSERVATORIO<br>MARBLE ORCHARD</h1>
  <div class="cover__visual" role="img" aria-label="Medaglione circolare con icone di media digitali"></div>
</section>

<section class="slide slide--white pos-b">
  <div class="break__art" role="img" aria-label="Scritta decorativa Take a Break su schizzi di colore"></div>
</section>

<section class="slide pos-c">
  <div class="brand" style="left:510px; top:12px;"><span class="brand__dot"></span><span class="brand__name">QUILLBROOK</span></div>
  <h2 class="index__title">INDICE</h2>
  <div class="index__row" style="left:33px; top:101px;">CAPITOLO 1</div><span class="index__num" style="left:184px; top:101px;">01</span>
  <div class="index__row" style="left:33px; top:140px;">CAPITOLO 1</div><span class="index__num" style="left:184px; top:140px;">04</span>
  <div class="index__row" style="left:33px; top:174px;">CAPITOLO 1</div><span class="index__num" style="left:184px; top:174px;">10</span>
  <div class="index__row" style="left:33px; top:212px;">CAPITOLO 1</div><span class="index__num" style="left:184px; top:212px;">15</span>
  <div class="index__row" style="left:237px; top:101px;">CAPITOLO 1</div><span class="index__num" style="left:387px; top:101px;">20</span>
  <div class="index__row" style="left:237px; top:140px;">CAPITOLO 1</div><span class="index__num" style="left:387px; top:140px;">24</span>
  <div class="index__row" style="left:237px; top:174px;">CAPITOLO 1</div><span class="index__num" style="left:387px; top:174px;">28</span>
</section>

<section class="slide pos-d">
  <h2 class="hopes__title">LE SPERANZE</h2>
  <p class="para" style="left:23px; top:56px; width:245px;">Il digitale semplificherà la nostra vita di cittadini»: ne sono convinti circa tre italiani su quattro in un trend che sembrava in diminuzione ma che è tornato a rafforzarsi durante l'emergenza del Covid-19, quando la tecnologia digitale ha mostrato di essere un abilitatore e facilitatore della vita privata, lavorativa e di cittadini in relazione con la pubblica amministrazione.</p>
  <h3 class="chart-title" style="left:24px; top:130px;">Il digitale semplifica la vita</h3>
  <svg class="chart" style="left:21px; top:148px;" viewBox="0 0 135 108" role="img" aria-label="Grafico: il digitale semplifica la vita">
    <g fill="var(--dot)" stroke="var(--dot-edge)" stroke-width="1">
      <circle cx="17" cy="56" r="8"/><circle cx="43" cy="63" r="8"/><circle cx="69" cy="74" r="8"/><circle cx="95" cy="57" r="8"/><circle cx="121" cy="53" r="8"/>
    </g>
    <g font-size="5" fill="#fff" text-anchor="middle">
      <text x="17" y="58">77%</text><text x="43" y="65">75%</text><text x="69" y="76">72%</text><text x="95" y="59">77%</text><text x="121" y="55">78%</text>
    </g>
    <g font-size="5.5" fill="#777" text-anchor="middle">
      <text x="17" y="104">feb 19</text><text x="43" y="104">ott 19</text><text x="69" y="104">feb 20</text><text x="95" y="104">mag 20</text><text x="121" y="104">nov 20</text>
    </g>
  </svg>
  <p class="para" style="left:294px; top:29px; width:246px;">I benefici della diffusione del digitale sulla qualità della vita all'interno delle case e nelle città sono evidenti a circa un italiano su due ma i temi «Smart Home» e «Smart Cities» sembrano aver perso la rilevanza che stavano guadagnando in periodo pre Covid.<br>L'entusiasmo per la democrazia partecipativa e per l'informazione diffusa, con i conseguenti benefici sul funzionamento del sistema democratico, non decolla e anche le aspettative relative all'emersione del «nero» grazie alla digitalizzazione dei processi amministrativi si stanno spegnendo col tempo: ci «crede» poco più di un italiano su tre.</p>
  <h3 class="chart-title" style="left:293px; top:149px;">Informazione più trasparente</h3>
  <svg class="chart" style="left:294px; top:170px;" viewBox="0 0 135 108" role="img" aria-label="Grafico: informazione più trasparente">
    <g fill="var(--dot)" stroke="var(--dot-edge)" stroke-width="1">
      <circle cx="17" cy="67" r="8"/><circle cx="43" cy="65" r="8"/><circle cx="69" cy="62" r="8"/><circle cx="95" cy="59" r="8"/><circle cx="121" cy="55" r="8"/>
    </g>
    <g font-size="5" fill="#fff" text-anchor="middle">
      <text x="17" y="69">48%</text><text x="43" y="67">49%</text><text x="69" y="64">50%</text><text x="95" y="61">52%</text><text x="121" y="57">53%</text>
    </g>
    <g font-size="5.5" fill="#777" text-anchor="middle">
      <text x="17" y="104">feb 19</text><text x="43" y="104">ott 19</text><text x="69" y="104">feb 20</text><text x="95" y="104">mag 20</text><text x="121" y="104">nov 20</text>
    </g>
  </svg>
</section>

<section class="slide pos-e">
  <div class="brand" style="left:502px; top:10px;"><span class="brand__dot"></span><span class="brand__name">QUILLBROOK</span></div>
  <h2 class="about__title">QUILLBROOK</h2>
  <div class="about__block" style="left:16px; top:92px;">
    <h3>INTRODUZIONE</h3>
    <p>Il digitale ha cambiato il mondo a un livello di profondità di cui non siamo ancora pienamente consapevoli. E' facile riconoscere le manifestazioni del digitale nei comportamenti delle persone e notare</p>
  </div>
  <div class="about__block" style="left:210px; top:92px;">
    <h3>LA RICERCA</h3>
    <p>"L'ambiente connesso è tutto ciò che accade perché siamo connessi alla rete: tutti i modi che, grazie alla connessione alla rete, abbiamo per comunicare con altre persone e tessere relazioni,</p>
  </div>
  <div class="about__block" style="left:16px; top:186px;">
    <h3>LE PAURE</h3>
    <p>Il digitale può fare paura per le conseguenze che produce nelle capacità cognitive, nelle relazioni personali e sociali, fino a quelle internazionali. Molti non conoscono cosa c'è dietro e da dove</p>
  </div>
  <div class="about__block" style="left:210px; top:186px;">
    <h3>LE PAURE</h3>
    <p>Otto persone su dieci ritengono che nell'ambiente digitale si siano diffuse pratiche di manipolazione delle persone più efficaci rispetto al passato. Il riferimento al passato è relativo al '900, epoca in cui i mezzi di</p>
  </div>
  <div class="about__rule-h"></div>
  <div class="about__rule-v"></div>
  <div class="about__node"></div>
  <div class="about__photo" role="img" aria-label="Fotografia: mano in rete poligonale che tocca una superficie di punti"></div>
</section>

<section class="slide pos-f">
  <div class="brand" style="left:12px; top:8px;"><span class="brand__dot"></span><span class="brand__name">QUILLBROOK</span></div>
  <h2 class="thanks">THANK YOU!</h2>
</section>

</body>
</html>
```